Creation of an elegant and modern turnkey Shopify website

Hello,

We are a new company specializing in the sale of above-ground pools. We want to create a turnkey website, ideally using Shopify. For now, we need a "showcase" site, not an e-commerce platform, with four tabs:

Home Page (an overall presentation of the company)
Our Products (an overview of all the above-ground pools we sell)
Our Projects (a page inspired by Instagram to showcase photos of our future projects)
Contact (a page with all our contact information and a contact form)

We are looking to create a highly visual, elegant, and modern website with vibrant splashes of color. We will provide the text, photos (along with instructions on where to place them on each page), and all other necessary information as attachments.

Thank you in advance for your proposals!

The Brisa Lagoon Team

Target Market(s)

Targeted at Swiss customers (a translator will need to be installed for different languages)

Industry/Entity Type

Sale of customised above-ground pools

Coding

Coded - Design and coding required

Font styles to use
Sans Serif

Colors
0094D4
00A9DD
6FCCEA
C7EBF8
E9F6FB
00AB8E
00BBA5
67D7C9
C6EFE9
E9F9F6

Requirements
Must have
• A stunning, elegant and modern look
Nice to have
• Inspiration from the colors of our logo throughout the site, but in an elegant way
Should not have
• An overly classic look for swimming pool sites

```html
<!DOCTYPE html>
<html lang="en">
<head>
<meta charset="utf-8">
<title>Brisa Lagoon – Above-Ground Pools</title>
<link href="https://fonts.googleapis.com/css2?family=Poppins:wght@400;500;600;700&display=swap" rel="stylesheet">
<style>
:root{
  --blue-deep:#0094D4;
  --blue:#00A9DD;
  --blue-soft:#6FCCEA;
  --blue-pale:#C7EBF8;
  --blue-mist:#E9F6FB;
  --ink:#1a1a1a;
  --text:#444;
  --white:#fff;
}
*{margin:0;padding:0;box-sizing:border-box}
html,body{width:1200px;height:3504px;overflow:hidden}
body{font-family:'Poppins',sans-serif;color:var(--text);background:var(--white);position:relative}
.block{position:absolute;left:0;width:1200px}
.btn{display:inline-block;background:var(--blue-deep);color:var(--white);font-size:15px;font-weight:500;padding:12px 30px;border-radius:24px;text-decoration:none}
.btn-light{background:var(--white);color:var(--blue-deep)}
.photo{position:absolute;border-radius:6px}
h2{font-weight:600;color:var(--ink);font-size:44px;line-height:1.2}
p{font-size:15px;line-height:1.75}

/* nav */
.site-nav{top:0;height:120px;display:flex;align-items:center}
.brand{position:absolute;left:110px;top:26px;font-size:30px;font-weight:500;color:var(--blue-deep);line-height:1;letter-spacing:2px}
.brand span{display:block}
.nav-links{position:absolute;left:505px;top:44px;display:flex;gap:56px;font-size:16px}
.nav-links a{color:var(--text);text-decoration:none}
.nav-links a.active{color:var(--blue-deep);border-bottom:2px solid var(--blue-deep);padding-bottom:6px}
.search{position:absolute;left:1060px;top:40px}

/* hero */
.hero{top:120px;height:540px;background:linear-gradient(120deg,#0a6fb0 0%,#1fa2dc 45%,#6FCCEA 100%)}
.hero-copy{position:absolute;left:112px;top:110px;width:560px;color:var(--white)}
.hero-copy h1{font-size:44px;font-weight:700;line-height:1.25;margin-bottom:22px}
.hero-copy p{font-size:17px;line-height:1.5;margin-bottom:28px;width:420px}

/* welcome */
.welcome{top:660px;height:520px;text-align:center}
.welcome h2{margin-top:105px}
.rule{width:110px;height:3px;background:var(--blue-soft);margin:16px auto 32px;border-radius:2px}
.welcome p{width:900px;margin:0 auto 36px}

/* services */
.services{top:1170px;height:370px;background:var(--blue-mist)}
.services .copy{position:absolute;left:112px;top:48px;width:440px}
.services h2{font-size:36px;white-space:nowrap;margin-bottom:16px}
.services p{font-size:14px;line-height:1.8;margin-bottom:22px}

/* guarantee */
.guarantee{top:1560px;height:500px}
.guarantee .copy{position:absolute;left:612px;top:118px;width:480px}
.guarantee h2{font-size:36px;white-space:nowrap;margin-bottom:16px}
.guarantee p{font-size:14px;line-height:1.8;margin-bottom:22px}

/* why */
.why{top:2060px;height:600px;background:linear-gradient(160deg,#0094D4 0%,#00A9DD 55%,#2fb8e6 100%);text-align:center;color:var(--white)}
.why h2{color:var(--white);font-size:46px;margin-top:75px}
.features{display:flex;justify-content:center;gap:30px;margin:50px auto 0;width:1040px}
.feature{width:230px}
.feature .icon{width:110px;height:110px;border-radius:50%;background:var(--white);margin:0 auto 22px;display:flex;align-items:center;justify-content:center}
.feature h3{font-size:21px;font-weight:600;margin-bottom:8px}
.feature p{font-size:13px;line-height:1.6}
.why .btn{margin-top:46px}

/* contact cta */
.cta{top:2660px;height:520px}
.cta .copy{position:absolute;left:112px;top:120px;width:460px}
.cta h2{font-size:44px;margin-bottom:18px}
.cta p{margin-bottom:26px}

/* footer */
.site-footer{top:3180px;height:270px;background:var(--blue-mist)}
.f-col{position:absolute;top:36px}
.f-col h4{font-size:22px;font-weight:600;color:var(--ink);margin-bottom:14px}
.f-col p,.f-col li{font-size:13px;line-height:1.7;list-style:none;color:var(--text)}
.f-contact{left:112px;width:270px}
.f-contact li{display:flex;align-items:center;gap:8px;margin-top:6px}
.f-quick{left:440px}
.f-other{left:600px}
.gallery{position:absolute;left:790px;top:36px;display:grid;grid-template-columns:145px 145px;gap:10px}
.gallery div{height:95px;border-radius:4px}
.copyright{top:3450px;height:54px;background:var(--blue-deep);color:var(--white);font-size:13px;display:flex;align-items:center;justify-content:space-between;padding:0 112px}
</style>
</head>
<body>

<header class="block site-nav">
  <div class="brand"><span>BRISA</span><span>LAGOON</span></div>
  <nav class="nav-links">
    <a class="active" href="#">Home</a>
    <a href="#">Our Products</a>
    <a href="#">Our Work</a>
    <a href="#">Contact Us</a>
  </nav>
  <svg class="search" width="26" height="26" viewBox="0 0 24 24" fill="none" stroke="#444" stroke-width="2"><circle cx="10" cy="10" r="7"/><line x1="15" y1="15" x2="21" y2="21"/></svg>
</header>

<section class="block hero" role="img" aria-label="Woman relaxing on a yellow ring float in clear blue pool water">
  <div class="hero-copy">
    <h1>Transform Your Garden With Our Premium Above-Ground Pools!</h1>
    <p>Achieve your dreams with our custom, tailor-made above-ground pools</p>
    <a class="btn btn-light" href="#">Get Started</a>
  </div>
</section>

<section class="block welcome">
  <h2>Welcome To Brisa Lagoon</h2>
  <div class="rule"></div>
  <p>Imagine an exceptional relaxation and leisure space right in your own backyard. With our unparalleled expertise and commitment to excellence, we create above-ground pools that exceed all expectations. Our exclusive, custom-designed models are crafted to combine style, durability, and innovation, offering a unique and refined experience.</p>
  <a class="btn" href="#">Read More</a>
</section>

<section class="block services">
  <div class="copy">
    <h2>Personalized Services</h2>
    <p>We understand that every garden and client is unique. That's why we offer personalized services, from design to installation and after-sales support. Our team of experts is here to answer all your questions and guide you throughout your project.</p>
    <a class="btn" href="#">Read More</a>
  </div>
  <div class="photo" role="img" aria-label="Rectangular above-ground pool with clear water" style="left:608px;top:100px;width:480px;height:170px;background:linear-gradient(135deg,#C7EBF8,#6FCCEA 60%,#00A9DD)"></div>
</section>

<section class="block guarantee">
  <div class="photo" role="img" aria-label="Woman swimming in a pool" style="left:112px;top:68px;width:436px;height:340px;background:linear-gradient(160deg,#2a6f88,#3f9fbf 55%,#7bc7dc)"></div>
  <div class="copy">
    <h2>Guaranteed Satisfaction</h2>
    <p>Your satisfaction is our top priority. We are committed to providing you with exceptional service and the highest quality products. Join our community of satisfied customers who are already enjoying their custom above-ground pools. 10-Year Warranty!</p>
    <a class="btn" href="#">Read More</a>
  </div>
</section>

<section class="block why">
  <h2>Why Choose<br>Our Above-Ground Pools?</h2>
  <div class="features">
    <div class="feature">
      <div class="icon"><svg width="54" height="54" viewBox="0 0 24 24" fill="none" stroke="#0094D4" stroke-width="1.6"><circle cx="12" cy="9" r="6"/><path d="M8.5 14l-2 7 5.5-3 5.5 3-2-7"/><path d="M9.5 9l2 2 3-3.5"/></svg></div>
      <h3>Superior Quality</h3>
      <p>Each pool is built with high-grade materials, ensuring exceptional durability and comfort.</p>
    </div>
    <div class="feature">
      <div class="icon"><svg width="54" height="54" viewBox="0 0 24 24" fill="none" stroke="#0094D4" stroke-width="1.6"><path d="M7 4v11M13 4v11M7 8h6M7 12h6"/><path d="M2 18c2 0 2-1.5 4-1.5s2 1.5 4 1.5 2-1.5 4-1.5 2 1.5 4 1.5 2-1.5 4-1.5"/></svg></div>
      <h3>Elegant Design</h3>
      <p>Our pools blend refined lines with modern finishes, becoming a true highlight of any garden.</p>
    </div>
    <div class="feature">
      <div class="icon"><svg width="54" height="54" viewBox="0 0 24 24" fill="none" stroke="#0094D4" stroke-width="1.6"><circle cx="12" cy="12" r="3.5"/><path d="M12 2v3M12 19v3M2 12h3M19 12h3M4.9 4.9l2.1 2.1M17 17l2.1 2.1M4.9 19.1L7 17M17 7l2.1-2.1"/></svg></div>
      <h3>Easy Installation</h3>
      <p>Enjoy a swift, hassle-free setup with our expert team handling every step of the process.</p>
    </div>
    <div class="feature">
      <div class="icon"><svg width="54" height="54" viewBox="0 0 24 24" fill="none" stroke="#0094D4" stroke-width="1.6"><path d="M9 17h6M10 20h4"/><path d="M8.5 14.5A6 6 0 1 1 15.5 14.5c-.7.6-1 1.3-1 2.5h-5c0-1.2-.3-1.9-1-2.5z"/></svg></div>
      <h3>Constant Innovation</h3>
      <p>We integrate the latest technologies to give you smart, efficient and lasting swimming pleasure.</p>
    </div>
  </div>
  <a class="btn btn-light" href="#">View More</a>
</section>

<section class="block cta">
  <div class="copy">
    <h2>Contact Us Today</h2>
    <p>Don't wait any longer to transform your garden into a wellness oasis. Contact us today to discover our range of customizable above-ground pools and get a tailored quote. Dive into a world of infinite possibilities with Brisa Lagoon!</p>
    <a class="btn" href="#">Contact Us</a>
  </div>
  <div class="photo" role="img" aria-label="Child floating on an orange ring in a bright blue pool" style="left:650px;top:80px;width:440px;height:340px;background:linear-gradient(145deg,#00A9DD,#6FCCEA 50%,#0094D4)"></div>
</section>

<footer class="block site-footer">
  <div class="f-col f-contact">
    <h4>Contact Us</h4>
    <p>Imagine an exceptional relaxation and leisure space right in your own backyard.</p>
    <ul>
      <li><svg width="14" height="14" viewBox="0 0 24 24" fill="#0094D4"><path d="M12 2a7 7 0 0 0-7 7c0 5 7 13 7 13s7-8 7-13a7 7 0 0 0-7-7zm0 9.5A2.5 2.5 0 1 1 12 6.5a2.5 2.5 0 0 1 0 5z"/></svg>8 Chemin du Lac, 1820 Montreux</li>
      <li><svg width="14" height="14" viewBox="0 0 24 24" fill="#0094D4"><path d="M6.6 10.8a15 15 0 0 0 6.6 6.6l2.2-2.2a1 1 0 0 1 1-.25 11.4 11.4 0 0 0 3.6.6 1 1 0 0 1 1 1V20a1 1 0 0 1-1 1A17 17 0 0 1 3 4a1 1 0 0 1 1-1h3.5a1 1 0 0 1 1 1c0 1.250.2 2.45.6 3.6a1 1 0 0 1-.25 1z"/></svg>079 000 12 34</li>
      <li><svg width="14" height="14" viewBox="0 0 24 24" fill="none"><path d="M3 5h18v14H3z" stroke="#0094D4" stroke-width="2"/><path d="M3 6l9 7 9-7" stroke="#0094D4" stroke-width="2"/></svg>hello@brisalagoon.ch</li>
    </ul>
  </div>
  <div class="f-col f-quick">
    <h4>Quick Links</h4>
    <ul><li>Home</li><li>About Us</li><li>Our Products</li><li>Our Works</li><li>Contact Us</li></ul>
  </div>
  <div class="f-col f-other">
    <h4>Other Links</h4>
    <ul><li>FAQs</li><li>Terms Of Services</li><li>Privacy Policy</li><li>Sitemaps</li><li>Help Center</li></ul>
  </div>
  <div class="gallery">
    <div role="img" aria-label="Pool by a house terrace" style="background:linear-gradient(135deg,#6FCCEA,#0094D4)"></div>
    <div role="img" aria-label="Family enjoying a garden pool" style="background:linear-gradient(135deg,#C7EBF8,#00A9DD)"></div>
    <div role="img" aria-label="Pool deck at sunset" style="background:linear-gradient(135deg,#00A9DD,#6FCCEA)"></div>
    <div role="img" aria-label="Above-ground pool in a green garden" style="background:linear-gradient(135deg,#0094D4,#C7EBF8)"></div>
  </div>
</footer>

<div class="block copyright">
  <span>Copyright © 2024 Brisa Lagoon. All Rights Reserved.</span>
  <svg width="14" height="14" viewBox="0 0 24 24" fill="none" stroke="#fff" stroke-width="2.5"><path d="M6 15l6-6 6 6"/></svg>
</div>

</body>
</html>
```